Business Card Design (NEW FILES)

ATTENTION: New vector files are available. Please update your design to reflect/use the new (better resolution) logo images.

Seeking a unique and professional business card design for a commercial drone photography/videography business. The layout should feature
the logo (attached) and include the following information:
Owen Tarrick
614-502-7738
www.skylarkreelworks.example
NRD Certified Remote Pilot

Owen Tarrick

```html
<!DOCTYPE html>
<html lang="en">
<head>
<meta charset="utf-8">
<title>Skylark Reelworks – Business Card</title>
<link href="https://fonts.googleapis.com/css2?family=Open+Sans:wght@400;600;700;800&display=swap" rel="stylesheet">
<style>
  :root {
    --stage: #222222;
    --paper: #ffffff;
    --navy: #1b1b4d;
    --orange: #ec8b53;
    --orange-deep: #e67a3e;
    --teal: #1fb3b5;
    --card-w: 540px;
    --card-h: 309px;
  }
  * { margin: 0; padding: 0; box-sizing: border-box; }
  html, body {
    width: 1200px; height: 780px; overflow: hidden;
    background: var(--stage);
    font-family: "Open Sans", sans-serif;
  }
  .sheet {
    width: 1200px; height: 780px;
    display: flex; align-items: center; justify-content: center; gap: 40px;
  }
  .card {
    position: relative;
    width: var(--card-w); height: var(--card-h);
    overflow: hidden;
    box-shadow: 0 10px 28px rgba(0,0,0,.45);
  }

  /* Front */
  .card-front { background: var(--paper); color: var(--navy); }
  .card-front .waves { position: absolute; inset: 0; width: 100%; height: 100%; }
  .wordmark {
    position: absolute; display: flex; align-items: center; gap: 8px;
    font-weight: 700; color: var(--navy); letter-spacing: .5px;
  }
  .card-front .wordmark { left: 150px; top: 30px; font-size: 24px; line-height: 1.05; }
  .wordmark .dot { width: 22px; height: 22px; border-radius: 50%; background: var(--orange); flex: none; }
  .contact {
    position: absolute; left: 46px; top: 104px;
    list-style: none; font-size: 13px; line-height: 1.65; color: var(--navy);
  }
  .contact li { display: flex; align-items: center; gap: 7px; }
  .contact svg { width: 11px; height: 11px; fill: var(--orange); flex: none; }
  .holder { position: absolute; right: 34px; top: 134px; text-align: right; }
  .holder .name { font-size: 28px; font-weight: 800; line-height: 1.1; }
  .holder .first { color: var(--orange); }
  .holder .last { color: var(--navy); }
  .holder .role { font-size: 14px; font-weight: 600; color: var(--navy); margin-top: 2px; }
  .edge-tab { position: absolute; right: 0; top: 178px; width: 14px; height: 62px; background: var(--orange); }
  .credentials {
    position: absolute; left: 128px; top: 262px; width: 196px;
    text-align: center; color: var(--paper); font-size: 13px; line-height: 1.45;
  }

  /* Back */
  .card-back { background: var(--orange); }
  .emblem-area {
    position: absolute; left: 120px; top: 20px; width: 400px; height: 230px;
    border-radius: 50%;
    background: radial-gradient(ellipse at 55% 50%, rgba(255,190,130,.55), rgba(230,122,62,.35) 60%, rgba(236,139,83,0) 75%);
  }
  .card-back .wordmark { left: 40px; top: 128px; font-size: 18px; }
  .card-back .wordmark .dot { width: 16px; height: 16px; background: var(--paper); }
</style>
</head>
<body>
<main class="sheet">

  <section class="card card-front" aria-label="Business card front">
    <svg class="waves" viewBox="0 0 540 309" aria-hidden="true">
      <path class="band-navy" d="M0,112 C8,212 80,238 190,245 C300,252 385,262 418,309 L0,309 Z" fill="var(--navy)"/>
      <path class="swoosh-teal" d="M14,92 C20,190 90,226 205,240 C95,232 28,200 22,96 Z" fill="var(--teal)"/>
      <path class="swoosh-orange" d="M170,232 C300,236 400,254 436,309 L424,309 C390,262 300,244 170,236 Z" fill="var(--orange)"/>
    </svg>

    <div class="wordmark"><span>Skylark<br>Reelworks</span><span class="dot"></span></div>

    <ul class="contact">
      <li>
        <svg viewBox="0 0 24 24"><path d="M6.6 10.8a15.1 15.1 0 0 0 6.6 6.6l2.2-2.2c.3-.3.7-.4 1-.2 1.1.4 2.3.6 3.6.6.6 0 1 .4 1 1V20c0 .6-.4 1-1 1A17 17 0 0 1 3 4c0-.6.4-1 1-1h3.5c.6 0 1 .4 1 1 0 1.3.2 2.5.6 3.6.1.3 0 .7-.2 1z"/></svg>
        614-502-7738
      </li>
      <li>
        <svg viewBox="0 0 24 24"><path d="M12 2a10 10 0 1 0 0 20 10 10 0 0 0 0-20zm6.9 6h-2.9a15.6 15.6 0 0 0-1.4-3.6A8 8 0 0 1 18.9 8zM12 4c.8 1.2 1.5 2.5 1.9 4h-3.8c.4-1.5 1.1-2.8 1.9-4zM4.3 14a8 8 0 0 1 0-4h3.4a16 16 0 0 0 0 4zm.8 2h2.9c.3 1.3.8 2.5 1.4 3.6A8 8 0 0 1 5.1 16zM8 8H5.1a8 8 0 0 1 4.3-3.6C8.8 5.5 8.3 6.7 8 8zm4 12c-.8-1.2-1.5-2.5-1.9-4h3.8c-.4 1.5-1.1 2.8-1.9 4zm2.3-6H9.7a14.7 14.7 0 0 1 0-4h4.6a14.7 14.7 0 0 1 0 4zm.3 5.6c.6-1.1 1.1-2.3 1.4-3.6h2.9a8 8 0 0 1-4.3 3.6zm1.7-5.6a16 16 0 0 0 0-4h3.4a8 8 0 0 1 0 4z"/></svg>
        www.skylarkreelworks.example
      </li>
    </ul>

    <div class="holder">
      <div class="name"><span class="first">Owen</span> <span class="last">Tarrick</span></div>
      <div class="role">Owner</div>
    </div>
    <div class="edge-tab"></div>

    <p class="credentials">NRD Certified Remote Pilot<br>Fully Insured</p>
  </section>

  <section class="card card-back" aria-label="Business card back">
    <div class="emblem-area" role="img" aria-label="Large embossed decoration of the company emblem"></div>
    <div class="wordmark"><span>Skylark<br>Reelworks</span><span class="dot"></span></div>
  </section>

</main>
</body>
</html>
```